Need Business Card for our Real Estate Business with Sales Executive's Picture

PANTONE 484 C ( RED)

PANTONE 2766 C ( BLUE

Industry/Entity Type

Real Estate

Contact Information for Business Card

Name, Mobile, email, & picture of Person
Agency Phone, address, Web address

Requirements
Must have
• Our Logo Colours, Agent Picture,

```html
<!DOCTYPE html>
<html lang="en">
<head>
<meta charset="utf-8">
<title>Meridian Real Estate – Business Card</title>
<link rel="stylesheet" href="https://fonts.googleapis.com/css2?family=Cinzel:wght@600&family=Questrial&display=swap">
<style>
  :root{
    --page:#1b1b1d;
    --navy:#1e2a5e;
    --navy-deep:#131b45;
    --navy-light:#2b3a78;
    --red:#8f1b2d;
    --red-light:#a82638;
    --white:#ffffff;
    --ink-soft:#dfe3f3;
  }
  *{box-sizing:border-box;margin:0;padding:0}
  html,body{width:1200px;height:864px;overflow:hidden;background:var(--page)}
  .sheet{position:relative;width:1200px;height:864px;display:flex;align-items:center;justify-content:center;gap:40px}
  .card{position:relative;width:540px;height:309px;overflow:hidden;box-shadow:0 10px 30px rgba(0,0,0,.6)}

  /* front */
  .card-front{background:var(--white)}
  .front-brand{position:absolute;top:72px;left:0;width:100%;display:flex;align-items:center;justify-content:center;gap:10px;
    font-family:"Cinzel",serif;font-weight:600;font-size:30px;letter-spacing:3px;color:var(--navy)}
  .brand-square{width:10px;height:10px;background:var(--red)}
  .name-band{position:absolute;top:140px;left:0;width:100%;height:42px;background:linear-gradient(180deg,var(--red-light),var(--red))}
  .agent-name{position:absolute;top:150px;left:118px;font-family:"Cinzel",serif;font-weight:600;font-size:21px;letter-spacing:1.5px;color:var(--white)}
  .contact-panel{position:absolute;top:182px;left:0;width:100%;height:127px;background:linear-gradient(160deg,var(--navy-light),var(--navy) 45%,var(--navy-deep))}
  .agent-photo{position:absolute;top:108px;left:418px;width:100px;height:100px;border-radius:50%;
    border:4px solid var(--white);box-shadow:0 0 0 2px var(--red);
    background:radial-gradient(circle at 50% 40%,#c9b3a4 0 22%,#2c3f86 23% 70%,#e9e9ec 71%)}
  .address{position:absolute;top:228px;left:36px;text-align:right;font-family:"Questrial",sans-serif;font-size:14px;line-height:18px;color:var(--ink-soft);letter-spacing:.5px}
  .contacts{position:absolute;top:196px;left:292px;list-style:none;font-family:"Questrial",sans-serif;font-size:13.5px;color:var(--white);letter-spacing:.6px}
  .contacts li{display:flex;align-items:center;gap:8px;height:20px}
  .contacts svg{width:12px;height:12px;fill:var(--ink-soft)}

  /* back */
  .card-back{background:linear-gradient(150deg,var(--navy-light),var(--navy) 50%,var(--navy-deep))}
  .tile-pattern{position:absolute;inset:0;background:linear-gradient(180deg,rgba(90,120,200,.18),rgba(90,120,200,.05) 60%,rgba(90,120,200,.15))}
  .back-brand{position:absolute;top:0;left:0;width:100%;height:100%;display:flex;align-items:center;justify-content:center;gap:12px;
    font-family:"Cinzel",serif;font-weight:600;font-size:30px;letter-spacing:3px;color:var(--white)}
  .back-brand .brand-square{background:var(--white)}
</style>
</head>
<body>
<main class="sheet">
  <section class="card card-front">
    <div class="front-brand"><span class="brand-square"></span>Meridian Real Estate</div>
    <div class="name-band"></div>
    <h1 class="agent-name">Daniel Crowe</h1>
    <div class="contact-panel"></div>
    <div class="agent-photo" role="img" aria-label="Portrait photo of the sales executive"></div>
    <p class="address">2280 Lakeview Road Suite 400<br>Oak Harbor, Il 60412</p>
    <ul class="contacts">
      <li><svg viewBox="0 0 12 12"><path d="M2.5 1l2 2-1 1.5c.8 1.6 2 2.8 3.5 3.5L8.5 7l2 2-1.5 2C5 10.5 1.5 7 1 3z"/></svg>(01) 555 0142</li>
      <li><svg viewBox="0 0 12 12"><path d="M3 0h6v12H3zM4 1.5v8h4v-8z"/></svg>020 555 0187</li>
      <li><svg viewBox="0 0 12 12"><path d="M0 2h12v8H0zM1 3v.3l5 3.5 5-3.5V3zM1 4.5V9h10V4.5L6 8z"/></svg>daniel@meridianrealty.com</li>
      <li><svg viewBox="0 0 12 12"><path d="M6 0a6 6 0 100 12A6 6 0 006 0zm0 1c.8 0 1.6 1.6 1.8 4.5H4.2C4.4 2.6 5.2 1 6 1zM1 6.5h2.2c.1 1.5.4 2.9.9 3.8A5 5 0 011 6.5zm0-1A5 5 0 014.1 1.7c-.5.9-.8 2.3-.9 3.8zm3.2 1h3.6C7.6 9.4 6.8 11 6 11s-1.6-1.6-1.8-4.5zm4.6 0H11a5 5 0 01-3.1 3.8c.5-.9.8-2.3.9-3.8zm0-1c-.1-1.5-.4-2.9-.9-3.8A5 5 0 0111 5.5z"/></svg>www.meridianrealty.com</li>
    </ul>
  </section>

  <section class="card card-back">
    <div class="tile-pattern" role="img" aria-label="Faint pattern of small window tiles across the card"></div>
    <div class="back-brand"><span class="brand-square"></span>Meridian Real Estate</div>
  </section>
</main>
</body>
</html>
```